Luxury Business Card Design for High-End Window Treatments

Gilded Slatworks
Custom Plantation Shutters & Architectural Shading Systems

⸻

BACK

Daniel Trevick
Owner

Custom Interior & Exterior Window Treatments

919-555-0148
gildedslatworks.com

I have included a picture that I’m hoping we can use on the back, but I’m also wondering if you can get rid of the ladder? Should we get rid of shutters , shades and blinds underneath Gilded Slatworks?

Target Market(s)

High-end residential homeowners, custom home builders, architects, interior designers, and luxury renovation clients seeking premium plantation shutters and motorized architectural shading systems.

Industry/Entity Type

Custom Window treatments

Contact Information for Business Card

Front Gilded Slatworks Custom Plantation Shutters Motorized Architectural Shading Systems BACK Daniel Trevick Owner 919-555-0148 GildedSlatworks.com Custom Interior & Exterior Window Treatments By Appointment

Requirements
Nice to have
• Not 100% sure on nice to halves or the color but you can definitely check out my website to get a better understanding of what I’m trying to do

```html
<!DOCTYPE html>
<html lang="en">
<head>
<meta charset="utf-8">
<title>Gilded Slatworks — Business Card</title>
<link href="https://fonts.googleapis.com/css2?family=Exo+2:wght@400;600;700&family=Prata&display=swap" rel="stylesheet">
<style>
  :root {
    --backdrop: #d9cfc2;
    --card-black: #121314;
    --card-charcoal: #2a2b2d;
    --gold: #c8ab5c;
    --gold-light: #d8c27a;
    --gold-muted: #b49a58;
    --text-soft: #cfc7b4;
    --sky: #4a8fd6;
    --sky-deep: #1f4f7e;
    --porch-navy: #182638;
    --stone: #6e5a44;
    --lawn: #3b4a2c;
  }
  * { box-sizing: border-box; margin: 0; padding: 0; }
  html, body {
    width: 1200px; height: 897px; overflow: hidden;
    background: var(--backdrop);
  }
  .business-card {
    position: absolute; left: 50px; top: 150px;
    width: 1100px; height: 598px;
    border-radius: 26px; overflow: hidden;
    background: linear-gradient(160deg, var(--card-charcoal) 0%, var(--card-black) 55%, #1b1c1e 100%);
    box-shadow: 0 18px 40px rgba(40, 30, 20, 0.35);
  }
  .card-photo {
    position: absolute; top: 0; right: 0; width: 690px; height: 100%;
    background:
      linear-gradient(180deg, transparent 0%, transparent 70%, var(--lawn) 92%, #2b3320 100%),
      linear-gradient(180deg, var(--sky) 0%, var(--sky-deep) 25%, var(--porch-navy) 40%, #1d2a3a 60%, var(--stone) 78%, transparent 100%);
  }
  .card-photo::after {
    content: ""; position: absolute; inset: 0;
    background: linear-gradient(90deg, var(--card-black) 0%, rgba(18,19,20,0.85) 12%, rgba(18,19,20,0.2) 32%, transparent 45%);
  }
  .brand { position: absolute; left: 73px; top: 70px; width: 320px; }
  .brand-name {
    font-family: "Prata", serif; color: var(--gold);
    font-size: 56px; line-height: 1.08; font-weight: 400;
    text-align: center;
  }
  .brand-services {
    margin-top: 14px;
    display: flex; justify-content: space-between;
    font-family: "Prata", serif; color: var(--gold-light);
    font-size: 24px;
  }
  .person { position: absolute; left: 70px; top: 316px; }
  .person-name {
    font-family: "Exo 2", sans-serif; font-weight: 700;
    font-size: 39px; color: var(--gold-light); letter-spacing: 0.5px;
  }
  .person-role {
    font-family: "Exo 2", sans-serif; font-size: 22px;
    color: var(--text-soft); letter-spacing: 1px; margin-top: -4px;
  }
  .contact-list { position: absolute; left: 70px; top: 425px; list-style: none; }
  .contact-item {
    display: flex; align-items: center; gap: 14px;
    font-family: "Exo 2", sans-serif; font-size: 23px;
    color: var(--text-soft); height: 39px;
  }
  .contact-item:first-child { color: #e2dccd; }
  .contact-icon { width: 20px; height: 20px; flex: none; }
</style>
</head>
<body>
  <main class="business-card">
    <div class="card-photo" role="img" aria-label="Photo of a stone-chimney house with a screened upper porch, columns, shrubs and lawn under a blue evening sky"></div>

    <section class="brand">
      <h1 class="brand-name">Gilded<br>Slatworks</h1>
      <p class="brand-services"><span>Shutters</span><span>Shades</span><span>Blinds</span></p>
    </section>

    <section class="person">
      <h2 class="person-name">Daniel Trevick</h2>
      <p class="person-role">Owner</p>
    </section>

    <ul class="contact-list">
      <li class="contact-item">
        <svg class="contact-icon" viewBox="0 0 20 20" aria-hidden="true">
          <rect x="5" y="1.5" width="10" height="17" rx="2" fill="none" stroke="var(--gold)" stroke-width="2"/>
          <rect x="8" y="14.5" width="4" height="1.6" fill="var(--gold)"/>
        </svg>
        <span>919-555-0148</span>
      </li>
      <li class="contact-item">
        <svg class="contact-icon" viewBox="0 0 20 20" aria-hidden="true">
          <rect x="1" y="4" width="18" height="12" rx="1" fill="var(--gold)"/>
          <path d="M1.5 4.5 L10 11 L18.5 4.5" fill="none" stroke="var(--card-black)" stroke-width="1.4"/>
        </svg>
        <span>Info@gildedslatworks.com</span>
      </li>
      <li class="contact-item">
        <svg class="contact-icon" viewBox="0 0 20 20" aria-hidden="true" fill="none" stroke="var(--gold-muted)" stroke-width="1.4">
          <circle cx="10" cy="10" r="8.5"/>
          <ellipse cx="10" cy="10" rx="3.8" ry="8.5"/>
          <line x1="1.5" y1="10" x2="18.5" y2="10"/>
          <line x1="3" y1="5.5" x2="17" y2="5.5"/>
          <line x1="3" y1="14.5" x2="17" y2="14.5"/>
        </svg>
        <span>www.gildedslatworks.com</span>
      </li>
    </ul>
  </main>
</body>
</html>
```